Website for Excavator and Earthworks Company

We require a modern, sleek and practical website for our newly created earthworks/excavator business in Perth, Western Australia called Bluegum Ridge Earthworks.

The website should have a modern, cutting edge feel but only needs to be relatively simplistic in it's layout and eventual functionality.

Some pages it should have would be Home, About, Projects and Contact Us.

```html
<!DOCTYPE html>
<html lang="en">
<head>
<meta charset="utf-8">
<title>Bluegum Ridge Earthworks</title>
<link rel="stylesheet" href="https://fonts.googleapis.com/css2?family=Teko:wght@500;600&family=Roboto:wght@400;500;700&family=Lato:wght@400&display=swap">
<style>
:root{
  --lime:#c8dc00;
  --ink:#0a0a0a;
  --white:#ffffff;
  --panel:#e4e4e4;
  --text:#333333;
  --muted:#555555;
  --rule:#222222;
}
*{box-sizing:border-box;margin:0;padding:0}
html,body{width:1200px;height:2738px;overflow:hidden;background:var(--white)}
body{position:relative;font-family:"Roboto",Arial,sans-serif;color:var(--ink)}
.abs{position:absolute}
.topline{left:0;top:0;width:1200px;height:4px;background:var(--lime)}
.brand{display:flex;align-items:center;gap:10px;font-family:"Roboto",Arial,sans-serif;font-weight:700;letter-spacing:.5px;white-space:nowrap}
.brand-mark{width:22px;height:22px;background:var(--lime)}
.site-header .brand{left:112px;top:36px;font-size:20px;color:var(--ink)}
.nav{display:flex;font-size:15px;font-weight:500;letter-spacing:.6px}
.site-header .nav{left:644px;top:29px;height:37px}
.nav a{color:inherit;text-decoration:none;display:flex;align-items:center;height:37px;padding:0 19px}
.nav a.active{background:var(--ink);color:var(--lime)}
.site-header .nav a:last-child{padding-right:0}
.hero{left:0;top:90px;width:1200px;height:513px;background:linear-gradient(100deg,#3c3f35 0%,#5b5a45 35%,#a0683a 65%,#c4824c 100%)}
.hero-photo{position:absolute;inset:0}
.hero h1{left:108px;top:212px;font-family:"Teko",sans-serif;font-weight:600;font-size:53px;line-height:54px;color:var(--white);letter-spacing:.5px;text-transform:uppercase}
.hl{color:var(--lime)}
.hero p{left:108px;top:346px;width:375px;font-size:15px;line-height:23px;font-weight:500;color:var(--white)}
.btn{display:flex;align-items:center;justify-content:center;font-size:15px;font-weight:500;letter-spacing:.5px;text-decoration:none;border:1px solid var(--ink);color:var(--ink)}
.hero .btn{left:110px;top:431px;width:177px;height:39px;border-color:var(--lime);color:var(--white)}
.section-title{left:0;width:1200px;text-align:center;font-family:"Teko",sans-serif;font-weight:600;font-size:54px;line-height:50px;letter-spacing:1px;text-transform:uppercase}
.divider{height:4px}
.divider::before{content:"";position:absolute;left:0;right:0;top:1.5px;height:1px;background:var(--rule)}
.divider span{position:absolute;top:0;height:4px;background:var(--lime)}
.section-sub{left:0;width:1200px;text-align:center;font-size:15px;color:var(--text)}
.service{top:829px;height:257px}
.service-tag{position:absolute;top:0;width:48px;height:257px;background:var(--ink)}
.service-tag span{position:absolute;left:50%;top:50%;transform:translate(-50%,-50%) rotate(-90deg);white-space:nowrap;font-family:"Teko",sans-serif;font-weight:500;font-size:22px;color:var(--white)}
.service-tag.lime{background:var(--lime)}
.service-tag.lime span{color:var(--ink)}
.service-photo{position:absolute;top:0;width:242px;height:257px}
.btn.view{left:537px;top:1122px;width:126px;height:40px}
.about{left:51px;top:1248px;width:1097px;height:595px;background:var(--panel)}
.about h2{left:111px;top:1328px;font-family:"Teko",sans-serif;font-weight:600;font-size:52px;line-height:50px;letter-spacing:.5px;text-transform:uppercase}
.about-lead{left:111px;top:1473px;width:510px;font-size:18px;line-height:26px;font-weight:500;color:var(--ink)}
.about-body{left:111px;top:1558px;width:507px;font-family:"Lato",sans-serif;font-size:14.5px;line-height:24.8px;color:var(--muted);text-align:justify}
.btn.read{left:112px;top:1717px;width:125px;height:39px}
.about-art{left:644px;top:1355px;width:446px;height:378px;background:radial-gradient(ellipse at 60% 45%,#dbe49a 0%,#e2e5c6 55%,var(--panel) 80%)}
.gallery-photo{position:absolute}
.site-footer{left:0;top:2604px;width:1200px;height:134px;background:var(--ink)}
.site-footer .brand{left:112px;top:2655px;font-size:26px;color:var(--white)}
.site-footer .brand-mark{width:26px;height:26px}
.site-footer .nav{left:644px;top:2629px;color:var(--white)}
.footer-rule{left:494px;top:2679px;width:596px;height:1px;background:#444}
.copyright{left:494px;top:2690px;width:596px;text-align:right;font-size:12.5px;color:var(--white)}
</style>
</head>
<body>
<div class="abs topline"></div>

<header class="site-header">
  <div class="abs brand"><span class="brand-mark"></span>BLUEGUM RIDGE EARTHWORKS</div>
  <nav class="abs nav">
    <a class="active" href="#">HOME</a><a href="#">ABOUT US</a><a href="#">PROJECTS</a><a href="#">CONTACT US</a>
  </nav>
</header>

<section class="abs hero">
  <div class="hero-photo" role="img" aria-label="Orange excavator digging into red earth at a Perth work site under a cloudy sky"></div>
</section>
<h1 class="abs hero-title" style="left:108px;top:212px;font-family:'Teko',sans-serif;font-weight:600;font-size:53px;line-height:54px;color:#fff;letter-spacing:.5px">RELIABLE <span class="hl">EARTHWORKS &amp;</span><br><span class="hl">EXCAVATION</span> IN PERTH, WA</h1>
<p class="abs" style="left:108px;top:346px;width:375px;font-size:15px;line-height:23px;font-weight:500;color:#fff">Residential, commercial and civil earthworks across Perth, delivering reliable excavation with precision, safety and efficiency.</p>
<a class="abs btn" href="#" style="left:110px;top:431px;width:177px;height:39px;border-color:var(--lime);color:#fff">REQUEST A QUOTE</a>

<h2 class="abs section-title" style="top:686px">What We Do</h2>
<div class="abs divider" style="left:526px;top:747px;width:149px"><span style="left:43px;width:63px"></span></div>
<p class="abs section-sub" style="top:777px">Reliable excavation and earthworks solutions for residential, commercial and civil projects across Perth.</p>

<div class="abs service" style="left:112px;width:296px">
  <div class="service-tag" style="left:0"><span>Trenching</span></div>
  <div class="service-photo" style="left:55px;background:linear-gradient(180deg,#b7c8d8 0%,#c9a77a 35%,#9c7a55 100%)" role="img" aria-label="Deep trench cut through sandy soil beside power poles"></div>
</div>
<div class="abs service" style="left:452px;width:296px">
  <div class="service-tag" style="left:0"><span>Footings &amp; Pads</span></div>
  <div class="service-photo" style="left:55px;background:linear-gradient(180deg,#a9a59c 0%,#c8c2b6 60%,#b4ab9c 100%)" role="img" aria-label="Timber formwork for concrete footings laid out on a cleared site"></div>
</div>
<div class="abs service" style="left:792px;width:297px">
  <div class="service-tag lime" style="left:0"><span>General Earthmoving</span></div>
  <div class="service-photo" style="left:55px;background:linear-gradient(180deg,#8fbf9a 0%,#78b08a 55%,#6c8f3a 100%)" role="img" aria-label="Excavator loading soil into a tipper truck"></div>
</div>

<a class="abs btn view" href="#">VIEW MORE</a>

<section class="abs about"></section>
<h2 class="abs" style="left:111px;top:1328px;font-family:'Teko',sans-serif;font-weight:600;font-size:52px;line-height:50px;letter-spacing:.5px">ABOUT BLUEGUM RIDGE<br>EARTHWORKS</h2>
<div class="abs divider" style="left:111px;top:1442px;width:365px"><span style="left:0;width:158px"></span></div>
<p class="abs about-lead">Perth-based Excavation And Earthworks Specialists Delivering Reliable Groundwork For Residential, Commercial And Civil Projects.</p>
<p class="abs about-body">Lorem ipsum dolor sit amet, consectetur adipiscing elit, sed do eiusmod tempor incididunt ut labore et dolore magna aliqua. Ut enim ad minim veniam, quis nostrud exercitation ullamco laboris nisi ut aliquip ex ea commodo consequat. Duis aute irure dolor in reprehenderit in voluptate velit esse cillum dolore eu fugiat nulla pariatur. Excepteur sint occaecat cupidatat non proident, sunt in culpa qui officia deserunt mollit anim id est laborum.</p>
<a class="abs btn read" href="#">READ MORE</a>
<div class="abs about-art" role="img" aria-label="Line drawing of an excavator on a mound of earth"></div>

<h2 class="abs section-title" style="top:1926px">Our Projects</h2>
<div class="abs divider" style="left:526px;top:1986px;width:149px"><span style="left:43px;width:63px"></span></div>
<p class="abs section-sub" style="top:2017px">Showcasing precision excavation and quality earthworks completed across Perth.</p>

<div class="gallery-photo" style="left:114px;top:2074px;width:227px;height:215px;background:linear-gradient(160deg,#c9c9cc 0%,#b0603c 50%,#8a4a2e 100%)" role="img" aria-label="Trencher attachment cutting into red soil"></div>
<div class="gallery-photo" style="left:114px;top:2298px;width:227px;height:220px;background:linear-gradient(180deg,#6f8a4a 0%,#7a8a50 45%,#b55a34 100%)" role="img" aria-label="Tipper truck unloading red earth in a field"></div>
<div class="gallery-photo" style="left:357px;top:2074px;width:324px;height:445px;background:linear-gradient(180deg,#4f5257 0%,#5d5f62 50%,#6a655c 100%)" role="img" aria-label="Excavator bucket on a building site with apartment blocks behind"></div>
<div class="gallery-photo" style="left:697px;top:2074px;width:392px;height:215px;background:linear-gradient(160deg,#d6d6d8 0%,#a85a38 55%,#9a4c2e 100%)" role="img" aria-label="Skid steer trencher digging a channel beside a shed"></div>
<div class="gallery-photo" style="left:697px;top:2298px;width:392px;height:220px;background:linear-gradient(120deg,#2e2520 0%,#6b4a35 50%,#a0704e 100%)" role="img" aria-label="Close view of excavator bucket teeth throwing up dust"></div>

<footer class="abs site-footer"></footer>
<div class="abs brand" style="left:112px;top:2655px;font-size:26px;color:#fff"><span class="brand-mark" style="width:26px;height:26px"></span>BLUEGUM RIDGE EARTHWORKS</div>
<nav class="abs nav" style="left:644px;top:2629px;color:#fff">
  <a href="#">HOME</a><a href="#">ABOUT US</a><a href="#">PROJECTS</a><a href="#" style="padding-right:0">CONTACT US</a>
</nav>
<div class="abs footer-rule"></div>
<p class="abs copyright">Copyright © 2026 Bluegum Ridge Earthworks. All rights reserved.</p>
</body>
</html>
```